I need a label design to go on our jars of honey. Our company is called Marrowdale Honey Co. The type of honey is called Fernlight Glen Honey. The jars are 1kg. Attached is the label size. Left hand side needs to have nutritional info... as attached. Middle section is our company name, honey type, 1kg & Kahurangi Bay, NZ. Right hand side needs to have info as per photo (raw honey etc). I would like to upload more pictures... but I’m unsure how to do this? Thanks, Carla

Target Market(s)

Honey consumers... families

Industry/Entity Type

Food Production

Colors

Designer to choose colors to be used in the design.

Requirements
Must have
• Nutritional info as per upload
• Type of honey & company name as per upload
• 1kg
• Address
Nice to have
• Similar fonts to upload.
• Possibly background image... floral or beach... very faint though.

```html
<!DOCTYPE html>
<html lang="en">
<head>
<meta charset="utf-8">
<title>Marrowdale Honey Co. – Fernlight Glen Honey label</title>
<link href="https://fonts.googleapis.com/css2?family=Roboto:ital,wght@0,300;0,400;1,300&display=swap" rel="stylesheet">
<style>
  :root {
    --paper: #ffffff;
    --terracotta: #c96a4f;
    --ink-light: #fdf3ee;
  }
  * { margin: 0; padding: 0; box-sizing: border-box; }
  html, body { width: 1200px; height: 1200px; overflow: hidden; background: var(--paper); }
  .canvas { position: relative; width: 1200px; height: 1200px; background: var(--paper); }

  .label {
    position: absolute; left: 0; top: 360px; width: 1200px; height: 480px;
    background: var(--terracotta); color: var(--ink-light);
    font-family: "Roboto", Arial, sans-serif; font-weight: 300;
  }
  .label__backdrop {
    position: absolute; left: 300px; top: 0; width: 640px; height: 480px;
    background:
      radial-gradient(ellipse 120px 110px at 310px 140px, rgba(232,160,128,.75), transparent 70%),
      radial-gradient(ellipse 130px 120px at 440px 320px, rgba(232,150,120,.7), transparent 72%),
      radial-gradient(ellipse 120px 120px at 160px 330px, rgba(225,140,110,.65), transparent 72%),
      radial-gradient(ellipse 90px 90px at 330px 160px, rgba(216,164,106,.5), transparent 70%),
      radial-gradient(ellipse 340px 260px at 320px 260px, rgba(160,80,70,.35), transparent 75%);
  }

  .left-panel { position: absolute; left: 0; top: 0; width: 400px; }
  .origin { position: absolute; left: 0; top: 25px; width: 400px; text-align: center; font-style: italic; font-size: 14px; line-height: 18px; }
  .nutrition {
    position: absolute; left: 60px; top: 65px; width: 266px; table-layout: fixed;
    border: 1.5px solid var(--ink-light); border-collapse: collapse; font-size: 11px;
  }
  .nutrition__intro { font-size: 8.5px; line-height: 12px; padding: 6px 6px 4px; border-bottom: 1.5px solid var(--ink-light); height: 48px; vertical-align: top; }
  .nutrition__head th { font-weight: 300; font-size: 7.5px; line-height: 12px; text-align: left; padding: 6px 4px 2px; border-bottom: 1.5px solid var(--ink-light); white-space: nowrap; }
  .nutrition__head th.col-100 { border-left: 1.5px solid var(--ink-light); }
  .nutrition td { padding: 0 6px; height: 25px; }
  .nutrition tbody tr:first-child td { padding-top: 6px; }
  .care { position: absolute; left: 0; top: 340px; width: 400px; text-align: center; font-style: italic; font-size: 12.5px; line-height: 15px; }
  .batch-box { position: absolute; left: 64px; top: 384px; width: 271px; height: 74px; background: var(--paper); color: #222; font-style: italic; font-size: 12.5px; line-height: 16px; padding: 9px 6px; }

  .centre { position: absolute; left: 400px; top: 0; width: 400px; text-align: center; }
  .brand { position: absolute; left: 0; top: 66px; width: 400px; font-size: 22px; letter-spacing: 4px; text-transform: uppercase; white-space: nowrap; }
  .variety { position: absolute; left: 0; top: 222px; width: 400px; font-size: 38px; line-height: 44px; white-space: nowrap; }
  .weight { position: absolute; left: 0; top: 360px; width: 400px; font-size: 24px; letter-spacing: 2px; }
  .weight-rule { position: absolute; left: 185px; top: 402px; width: 30px; height: 2px; background: var(--ink-light); }
  .place { position: absolute; left: 0; top: 424px; width: 400px; font-size: 22px; letter-spacing: 3px; white-space: nowrap; }

  .right-panel { position: absolute; left: 870px; top: 0; width: 285px; text-align: center; font-size: 17px; line-height: 20px; }
  .right-panel p { position: absolute; left: 0; width: 285px; }
  .story-1 { top: 52px; } .story-2 { top: 112px; } .story-3 { top: 192px; } .story-4 { top: 252px; }
  .divider { position: absolute; left: 34px; top: 342px; width: 218px; height: 2px; background: var(--ink-light); }
  .contact { top: 356px; }
</style>
</head>
<body>
<div class="canvas">
  <section class="label">
    <div class="label__backdrop" role="img" aria-label="Faint photograph of soft pink blossom flowers"></div>

    <div class="left-panel">
      <p class="origin">100% New Zealand Honey<br>No added ingredients</p>
      <table class="nutrition">
        <colgroup><col style="width:118px"><col style="width:70px"><col style="width:78px"></colgroup>
        <tr><td class="nutrition__intro" colspan="3">NUTRITIONAL INFORMATION<br>Serving per package: 100<br>Serving size: 10g</td></tr>
        <tr class="nutrition__head"><th></th><th>Average Quantity<br>per Serving</th><th class="col-100">Average Quantity<br>per 100g</th></tr>
        <tbody>
          <tr><td>Energy</td><td>134kj</td><td>1340kj</td></tr>
          <tr><td>Protein</td><td>0.04g</td><td>0.4g</td></tr>
          <tr><td>Fat Total</td><td>0g</td><td>0g</td></tr>
          <tr><td>- saturated</td><td>0g</td><td>0g</td></tr>
          <tr><td>Carbohydrate</td><td>7.9g</td><td>79.6g</td></tr>
          <tr><td>- sugars</td><td>7.8g</td><td>78.1g</td></tr>
          <tr><td>Sodium</td><td>1.2mg</td><td>12mg</td></tr>
        </tbody>
      </table>
      <p class="care">Store upright in a cool, dry place. No refrigeration needed.<br>Not recommended for infants below the age of 12 months.</p>
      <div class="batch-box">Best before:<br>RMP:<br>Batch No:</div>
    </div>

    <div class="centre">
      <p class="brand">Marrowdale Honey Co.</p>
      <p class="variety">Fernlight Glen Honey</p>
      <p class="weight">1KG</p>
      <div class="weight-rule"></div>
      <p class="place">KAHURANGI BAY, N.Z.</p>
    </div>

    <div class="right-panel">
      <p class="story-1">Sourced from the beautiful<br>Tawhiri Coast.</p>
      <p class="story-2">Our honey comes to you raw &amp;<br>unpasteurised, ensuring it retains all<br>natural goodness!</p>
      <p class="story-3">Arohanui,<br>Rowan, Carla &amp; boys</p>
      <p class="story-4">‘Marrowdale’ all thanks to God for His<br>incredible creation!</p>
      <div class="divider"></div>
      <p class="contact">www.marrowdalehoney.co.nz<br>42 Kereru Lane<br>Kahurangi Bay, New Zealand</p>
    </div>
  </section>
</div>
</body>
</html>
```